Business Card and Letterhead for Pimlu - modern real estate business

I need a double sided business card design for Pimlu. Please see business card brief here https://files.trelvonadocs.com/sheet/r/7QzTmWbaXLJnoPEd-kRyUgFhHsstbvCe2qfoMxDa_pz/view?mode=shared

Please feel free to design the business cards however you feel best. I am happy to give some creative freedoms and then provide feedback from there.

Please then also create a letterhead to match the business card design

Colors

Designer to choose colors to be used in the design.

Requirements
Must have
• Must be a modern, elegant business card which looks very professional

```html
<!DOCTYPE html>
<html lang="en">
<head>
<meta charset="utf-8">
<title>Pimlu – Business Card and Letterhead</title>
<link rel="stylesheet" href="https://fonts.googleapis.com/css2?family=Lato:wght@400;700&display=swap">
<style>
  :root {
    --brand-red: #e42229;
    --charcoal: #3d4640;
    --ink: #1d1d1d;
    --paper: #ffffff;
    --backdrop: #ecebe8;
    --photo-light: #9fae8a;
    --photo-dark: #3b3f3a;
  }
  * { box-sizing: border-box; margin: 0; padding: 0; }
  html, body { width: 1200px; height: 900px; overflow: hidden; }
  body {
    background: var(--backdrop);
    font-family: "Lato", sans-serif;
    color: var(--ink);
    position: relative;
  }

  /* Letterhead */
  .letterhead {
    position: absolute; left: 132px; top: 112px;
    width: 493px; height: 698px;
    background: var(--paper);
    box-shadow: 0 3px 10px rgba(0,0,0,.18);
    overflow: hidden;
  }
  .wordmark {
    font-family: "Lato", sans-serif;
    font-weight: 700;
    color: var(--brand-red);
    letter-spacing: 2px;
    line-height: 1;
  }
  .letterhead .wordmark {
    position: absolute; left: 25px; top: 27px; font-size: 36px;
  }
  .contact-list { list-style: none; }
  .contact-list li {
    display: flex; align-items: center; gap: 7px;
  }
  .contact-list svg { flex: none; }
  .letterhead .contact-list {
    position: absolute; left: 353px; top: 22px;
    font-size: 10px;
  }
  .letterhead .contact-list li { height: 14px; }

  .letter-body {
    position: absolute; left: 47px; top: 175px; width: 401px;
    font-size: 9.5px; line-height: 12px;
  }
  .letter-body .salutation { font-weight: 700; margin-bottom: 18px; }
  .letter-body p.paragraph { text-align: justify; margin-bottom: 24px; }
  .letter-body .sign-off { font-weight: 700; line-height: 13.2px; margin-top: 24px; }

  .letter-footer {
    position: absolute; left: 0; bottom: 0; width: 493px; height: 64px;
  }
  .letter-footer svg { position: absolute; inset: 0; }
  .letter-footer address {
    position: absolute; left: 18px; bottom: 11px;
    font-style: normal; color: var(--paper);
    font-size: 9px; line-height: 11px;
  }

  /* Business card front */
  .card {
    position: absolute; width: 409px; height: 245px;
    box-shadow: 0 3px 10px rgba(0,0,0,.2);
    overflow: hidden;
  }
  .card-front { left: 713px; top: 170px; background: var(--paper); }
  .card-photo {
    position: absolute; left: 35px; top: 50px;
    width: 144px; height: 144px; border-radius: 50%;
    border: 2px solid var(--brand-red);
    background: radial-gradient(circle at 50% 30%, var(--photo-light) 0%, #7d8a6b 45%, var(--photo-dark) 100%);
  }
  .card-divider {
    position: absolute; left: 205px; top: 50px;
    width: 1px; height: 144px; background: var(--brand-red);
  }
  .card-details { position: absolute; left: 227px; top: 54px; }
  .card-name {
    font-size: 19px; font-weight: 700; color: var(--brand-red); line-height: 22px;
  }
  .card-role { font-size: 11.4px; line-height: 14px; margin-top: 1px; }
  .card-details address {
    font-style: normal; font-size: 11.4px; line-height: 13px; margin-top: 11px;
  }
  .card-details .contact-list { font-size: 11.4px; margin-top: 10px; }
  .card-details .contact-list li { height: 15.6px; }
  .card-wave { position: absolute; left: 0; bottom: 0; width: 409px; height: 45px; }

  /* Business card back */
  .card-back {
    left: 712px; top: 461px; height: 249px;
    background: var(--brand-red);
    display: flex; align-items: center; justify-content: center;
  }
  .card-back .wordmark {
    color: var(--paper); font-size: 66px; letter-spacing: 5px;
  }
</style>
</head>
<body>

<article class="letterhead">
  <div class="wordmark">PIMLU</div>
  <ul class="contact-list">
    <li><svg width="10" height="10" viewBox="0 0 10 10"><path d="M2.2 1 L3.8 2.8 L2.9 4 Q4 6.2 6 7.1 L7.2 6.2 L9 7.8 L7.8 9.2 Q3.6 8.6 0.9 2.2 Z" fill="var(--brand-red)"/></svg>0412 583 190</li>
    <li><svg width="10" height="10" viewBox="0 0 10 10"><rect x="0.5" y="2" width="9" height="6.5" fill="var(--brand-red)"/><path d="M0.8 2.3 L5 5.6 L9.2 2.3" stroke="#fff" stroke-width="0.9" fill="none"/></svg>dane@pimlu.com</li>
    <li><svg width="10" height="10" viewBox="0 0 10 10" fill="none" stroke="var(--brand-red)" stroke-width="0.8"><circle cx="5" cy="5" r="4.3"/><ellipse cx="5" cy="5" rx="1.9" ry="4.3"/><path d="M0.7 5 H9.3 M1.4 2.8 H8.6 M1.4 7.2 H8.6"/></svg>www.pimlu.com</li>
  </ul>

  <div class="letter-body">
    <p class="salutation">Dear Sir/Mam,</p>
    <p class="paragraph">Contrary to popular belief, Lorem Ipsum is not simply random text. It has roots in a piece of classical Latin literature from 45 BC, making it over 2000 years old. Walter Brennick, a Latin professor at Ashgrove College in Vermont, looked up one of the more obscure Latin words, consectetur, from a Lorem Ipsum passage, and going through the cites of the word in classical literature, discovered the undoubtable source.</p>
    <p class="paragraph">Lorem Ipsum comes from sections 1.10.32 and 1.10.33 of "de Finibus Bonorum et Malorum" (The Extremes of Good and Evil) by Marcus Tellan, written in 45 BC. This book is a treatise on the theory of ethics, very popular during the Renaissance. The first line of Lorem Ipsum, "Lorem ipsum dolor sit amet..", comes from a line in section 1.10.32.</p>
    <p class="paragraph">The standard chunk of Lorem Ipsum used since the 1500s is reproduced below for those interested. Sections 1.10.32 and 1.10.33 from "de Finibus Bonorum et Malorum" by Marcus Tellan are also reproduced in their exact original form, accompanied by English versions from the 1914 translation by H. Dellow.</p>
    <p class="paragraph">The standard chunk of Lorem Ipsum used since the 1500s is reproduced below for those interested.</p>
    <p class="sign-off">Best Regards<br>Dane Morrow<br>Licenced Real Estate Agent</p>
  </div>

  <footer class="letter-footer">
    <svg viewBox="0 0 493 64" width="493" height="64" preserveAspectRatio="none">
      <path d="M0 8 Q250 60 493 0 L493 64 L0 64 Z" fill="var(--brand-red)"/>
      <path d="M160 26 Q330 40 493 16 L493 21 Q330 44 160 26 Z" fill="var(--paper)"/>
      <path d="M170 28 Q330 42 493 19 L493 22 Q330 45 170 28 Z" fill="var(--charcoal)"/>
      <path d="M160 25 Q330 38 493 14 L493 16 Q330 40 160 25 Z" fill="var(--brand-red)"/>
    </svg>
    <address>PO Box 3071<br>Glenrowan NSW 2790</address>
  </footer>
</article>

<section class="card card-front">
  <div class="card-photo" role="img" aria-label="Portrait photo of the agent"></div>
  <div class="card-divider"></div>
  <div class="card-details">
    <h1 class="card-name">Dane Morrow</h1>
    <p class="card-role">Licenced Real Estate Agent</p>
    <address>PO Box 3071<br>Glenrowan NSW 2790</address>
    <ul class="contact-list">
      <li><svg width="12" height="12" viewBox="0 0 10 10"><path d="M2.2 1 L3.8 2.8 L2.9 4 Q4 6.2 6 7.1 L7.2 6.2 L9 7.8 L7.8 9.2 Q3.6 8.6 0.9 2.2 Z" fill="var(--brand-red)"/></svg>0412 583 190</li>
      <li><svg width="12" height="12" viewBox="0 0 10 10"><rect x="0.5" y="2" width="9" height="6.5" fill="var(--brand-red)"/><path d="M0.8 2.3 L5 5.6 L9.2 2.3" stroke="#fff" stroke-width="0.9" fill="none"/></svg>dane@pimlu.com</li>
      <li><svg width="12" height="12" viewBox="0 0 10 10" fill="none" stroke="var(--brand-red)" stroke-width="0.8"><circle cx="5" cy="5" r="4.3"/><ellipse cx="5" cy="5" rx="1.9" ry="4.3"/><path d="M0.7 5 H9.3 M1.4 2.8 H8.6 M1.4 7.2 H8.6"/></svg>www.pimlu.com</li>
    </ul>
  </div>
  <svg class="card-wave" viewBox="0 0 409 45" preserveAspectRatio="none">
    <path d="M0 5 Q200 40 409 0 L409 45 L0 45 Z" fill="var(--brand-red)"/>
    <path d="M135 26 Q280 34 409 12 L409 18 Q280 38 135 26 Z" fill="var(--paper)"/>
    <path d="M140 27 Q280 36 409 15 L409 19 Q280 40 140 27 Z" fill="var(--charcoal)"/>
    <path d="M135 25 Q280 32 409 10 L409 13 Q280 35 135 25 Z" fill="var(--brand-red)"/>
  </svg>
</section>

<section class="card card-back">
  <div class="wordmark">PIMLU</div>
</section>

</body>
</html>
```